Updated website design needed for Radiology Group, Pine Hollow Imaging Partners

Clean, uncluttered, updated design needed for top regional Radiology Center. Focus on personal, patient oriented design, (not clinical). Should be simple and easy to navigate, with clear CTAs. Use blues, greens and photos of people in the Central Oregon outdoors.
Uncoded, PSD design only. 2 pages: Home page and one example interior page.
reference current site: http://www.phipclinic-example.com/
Sites they like:
http://www.valescanlabs-example.com/
http://www.tbmx-example.net/handler.cfm?event=practice,main
http://www.kestrelbonecare-example.com/

Medical Imaging

2 page

Sans Serif

• Personal and patient friendly.
• Lots of white space, clean and uncluttered. Clear CTAs, such as: Patient Bill Pay, Make an Appointment, Meet Our Doctors
• Use copy and contact information from the current site.
• Use outdoor images from Central Oregon, late Winter/ Spring (snow, light colors, spring green, for example)
• Include one example interior page, either Your Exam or Meet Our Doctors
• The client likes:
• Meet Our Doctors slider section, and big, easy to navigate Information Center on www.kestrelbonecare-example.com
• The personal feel of the Your Exam section on www.valescanlabs-example.com
• Blues and Greens, outdoorsy imagery
• The client does not like:
• complex drop down menus
• clinical feel
• Do not use lorum ipsum or dummy text.
• Do not use outdoor images from other regions. Do not use Summer (hot, poolside) or Fall (red/orange leaves) images.

```html
<!DOCTYPE html>
<html lang="en">
<head>
<meta charset="utf-8">
<title>Pine Hollow Imaging Partners</title>
<link href="https://fonts.googleapis.com/css2?family=Open+Sans:wght@400;600;700&family=Raleway:wght@400;500;600;700&display=swap" rel="stylesheet">
<style>
:root{
  --blue:#4384ea;
  --blue-deep:#3a72d8;
  --blue-dark:#2f62c9;
  --green:#48d6a4;
  --ink:#1e1e22;
  --text:#4a4a4f;
  --muted:#8d8d93;
  --pale:#f6f8fd;
  --white:#ffffff;
}
*{margin:0;padding:0;box-sizing:border-box}
html,body{width:735px;height:1200px;overflow:hidden}
body{position:relative;background:var(--white);font-family:"Open Sans",sans-serif;color:var(--text)}
.abs{position:absolute}
a{color:inherit;text-decoration:none}

/* header */
.brand{left:54px;top:9px;display:flex;align-items:center;gap:5px}
.brand-mark{width:28px;height:28px;background:var(--blue)}
.brand-name{font-size:9px;font-weight:600;color:#3b3b5c;width:76px;line-height:1.15}
.util{top:19px;font-size:7.4px;color:var(--ink);display:flex;align-items:center;gap:4px}
.util svg{width:8px;height:8px}
.cta{left:553px;top:9px;width:127px;height:27px;border-radius:14px;background:var(--green);color:var(--white);font-size:7.4px;display:flex;align-items:center;justify-content:center;gap:5px}

/* nav */
.nav{left:0;top:45px;width:735px;height:31px;background:var(--blue);display:flex;padding-left:54px}
.nav a{font-size:6.8px;font-weight:600;color:var(--white);padding:0 8px;line-height:31px}
.nav a.active{background:var(--white);color:var(--blue);padding:0 11px}

/* hero */
.hero{left:0;top:76px;width:735px;height:254px;overflow:hidden}
.hero-photo{position:absolute;inset:0;background:linear-gradient(120deg,#e9e2d8 30%,#d6b98a 60%,#c9a26c 80%,#e7dccd)}
.hero-title{left:54px;top:76px;font-family:"Raleway",sans-serif;font-weight:700;font-size:33px;color:var(--white);line-height:1}
.hero-sub{left:54px;top:115px;font-family:"Raleway",sans-serif;font-size:17px;color:var(--white)}
.hero-btn{left:54px;top:142px;width:90px;height:25px;border:1px solid var(--white);border-radius:13px;color:var(--white);font-size:7px;font-weight:600;display:flex;align-items:center;justify-content:center}
.round-arrow{width:21px;height:21px;border-radius:50%;background:var(--white);display:flex;align-items:center;justify-content:center}

/* about */
.about-frame{left:65px;top:361px;width:200px;height:199px;background:var(--blue)}
.about-photo{left:54px;top:370px;width:200px;height:199px;background:linear-gradient(135deg,#bcb3a6,#ece8e0 50%,#d8d2c6)}
.h2{font-family:"Raleway",sans-serif;font-weight:600;font-size:16.5px;color:var(--ink)}
.h2 em{font-style:normal;color:var(--blue)}
.about-copy{left:290px;top:380px;width:392px;font-size:6.9px;line-height:13.6px}
.about-copy p+p{margin-top:13.6px}
.outline-btn{border:1px solid var(--blue-deep);border-radius:13px;color:var(--blue-deep);font-size:7px;display:flex;align-items:center;justify-content:center}

/* testimonials */
.quotes{left:0;top:614px;width:735px;height:209px;background:var(--pale)}
.quote-card{top:673px;width:270px;height:93px;background:var(--white);border:1px solid #e3e7f0}
.quote-card p{position:absolute;left:23px;top:26px;width:230px;font-size:8.2px;line-height:13.6px;color:var(--muted)}
.qmark{font-family:Georgia,serif;font-weight:700;font-size:14px;color:var(--blue);line-height:1}
.avatar{width:60px;height:60px;border-radius:50%;border:2px solid var(--blue)}
.client-name{top:776px;font-family:"Raleway",sans-serif;font-weight:600;font-size:8.2px;color:#444;letter-spacing:.3px}
.dot{left:675px;width:6px;height:6px;border-radius:50%;background:var(--blue)}

/* doctors */
.doc-ring{left:296px;top:851px;width:142px;height:142px;border-radius:50%;background:#8fb1ef}
.doc-inner{left:302px;top:857px;width:130px;height:130px;border-radius:50%;background:var(--blue-deep)}
.doc-photo{left:309px;top:864px;width:116px;height:116px;border-radius:50%;background:radial-gradient(circle at 50% 45%,#8a7668,#4a4a4c 60%,#2c2c2e)}
.zoom{left:352px;top:907px;width:30px;height:30px;border-radius:50%;background:var(--white);display:flex;align-items:center;justify-content:center}
.nav-circle{width:23px;height:23px;border-radius:50%;display:flex;align-items:center;justify-content:center}

/* footer */
.footer{left:0;top:1022px;width:735px;height:154px;background:linear-gradient(180deg,#5b8fe2,#3d78df)}
.foot-col{top:1040px;color:var(--white)}
.foot-col h4{font-size:7.8px;font-weight:600;margin-bottom:5px}
.foot-col li{list-style:none;font-size:7px;line-height:13.6px;display:flex;align-items:center;gap:4px}
.foot-col li::before{content:"";width:2px;height:2px;border:0.6px solid var(--white);border-radius:50%}
.foot-col.contact li{line-height:19px;gap:7px}
.foot-col.contact li::before{display:none}
.foot-col.contact svg{width:7px;height:7px}
.copyright{left:0;top:1176px;width:735px;height:24px;background:var(--blue-dark);color:var(--white);font-size:6.8px;display:flex;align-items:center;justify-content:center}
</style>
</head>
<body>

<header>
  <a class="abs brand" href="#"><span class="brand-mark"></span><span class="brand-name">Pine Hollow Imaging Partners</span></a>
  <a class="abs util" style="left:360px" href="#">
    <svg viewBox="0 0 10 10"><circle cx="5" cy="3" r="2.2" fill="#222"/><path d="M1 10 Q1 5.5 5 5.5 Q9 5.5 9 10Z" fill="#222"/></svg>MEET OUR DOCTORS</a>
  <a class="abs util" style="left:461px" href="#">
    <svg viewBox="0 0 10 10"><rect x="0.5" y="2" width="9" height="6" rx="1" fill="#222"/><rect x="0.5" y="4" width="9" height="1.2" fill="#fff"/></svg>PATIENT BILL PAY</a>
  <a class="abs cta" href="#">
    <svg width="8" height="8" viewBox="0 0 10 10"><rect x="1" y="2" width="8" height="7" fill="none" stroke="#fff"/><line x1="1" y1="4" x2="9" y2="4" stroke="#fff"/></svg>MAKE AN APPOINTMENT</a>
</header>

<nav class="abs nav">
  <a class="active" href="#">HOME</a><a href="#">ABOUT US</a><a href="#">OUR SERVICES</a><a href="#">FOR PATIENTS</a><a href="#">OUR PHYSICIANS</a><a href="#">FOR PHYSICIANS</a><a href="#">PACS &amp; DOCUMENTS</a><a href="#">APPOINTMENTS</a><a href="#">OUR LOCATIONS</a>
</nav>

<section class="abs hero">
  <div class="hero-photo" role="img" aria-label="Photo of a technologist in safety glasses and mask at work"></div>
  <svg class="abs" style="left:0;top:0" width="735" height="254" viewBox="0 0 735 254">
    <defs><linearGradient id="heroBlue" x1="0" y1="0" x2="0.4" y2="1"><stop offset="0" stop-color="#6fb0dc"/><stop offset="1" stop-color="#3f7ee0"/></linearGradient></defs>
    <path d="M0 0 H351 Q400 60 384 128 Q372 200 338 254 H0Z" fill="url(#heroBlue)"/>
  </svg>
  <h1 class="abs hero-title">Welcome to</h1>
  <p class="abs hero-sub">Pine Hollow Imaging Partners</p>
  <a class="abs hero-btn" href="#">Learn More</a>
  <a class="abs round-arrow" style="left:16px;top:117px" href="#"><svg width="6" height="6" viewBox="0 0 6 6"><path d="M4 1 L2 3 L4 5" fill="none" stroke="#3a72d8" stroke-width="1"/></svg></a>
  <a class="abs round-arrow" style="left:698px;top:117px" href="#"><svg width="6" height="6" viewBox="0 0 6 6"><path d="M2 1 L4 3 L2 5" fill="none" stroke="#3a72d8" stroke-width="1"/></svg></a>
</section>

<section>
  <div class="abs about-frame"></div>
  <div class="abs about-photo" role="img" aria-label="Photo of gloved hands holding a sample vial"></div>
  <h2 class="abs h2" style="left:290px;top:349px">About <em>Us</em></h2>
  <div class="abs about-copy">
    <p>Pine Hollow Imaging Partners is a diagnostic imaging corporation providing professional services to Central and Eastern Oregon hospitals and clinics as well as state-of-the-art services in its' own outpatient imaging center. PHIP was established by its' founder, Harold M. Brecken, MD when he opened his Central Oregon practice in 1947.</p>
    <p>PHIP is staffed by fellowship trained physicians with expertise in major disciplines to include mammography, ultrasound, Magnetic Resonance Imaging, Computed Tomography, Positron Emission Tomography, interventional procedures, Nuclear Medicine and general procedures which include fluoroscopy, tomography, IVP's and radiographic procedures for head, chest, abdomen and extremity examinations. All technologists have advanced level training and certifications in modalities they specialize in. Each of our imaging modalities has either been granted National Board of Imaging Standards accreditation or is in the process of doing so. This rigorous process provides a stamp of approval for the entire imaging process, including the equipment, quality control program, record keeping and staff qualifications.</p>
  </div>
  <a class="abs outline-btn" style="left:290px;top:559px;width:79px;height:24px" href="#">Read More</a>
</section>

<section>
  <div class="abs quotes"></div>
  <h2 class="abs h2" style="left:0;top:636px;width:735px;text-align:center">The client <em>likes</em></h2>

  <div class="abs quote-card" style="left:54px">
    <span class="abs qmark" style="left:10px;top:16px">&ldquo;</span>
    <p>I couldn't believe how smoothly it went. I'm a new man. It's wonderful to have all that freedom without pain anymore.</p>
    <span class="abs qmark" style="left:246px;top:55px">&rdquo;</span>
  </div>
  <div class="abs avatar" style="left:66px;top:739px;background:linear-gradient(135deg,#7a8aa8,#c9b8a8)" role="img" aria-label="Client portrait"></div>
  <span class="abs client-name" style="left:136px">CLIENT NAME HERE</span>

  <div class="abs quote-card" style="left:360px">
    <span class="abs qmark" style="left:10px;top:16px">&ldquo;</span>
    <p>I couldn't believe how smoothly it went. I'm a new man. It's wonderful to have all that freedom without pain anymore.</p>
    <span class="abs qmark" style="left:246px;top:55px">&rdquo;</span>
  </div>
  <div class="abs avatar" style="left:372px;top:739px;background:linear-gradient(135deg,#e8ecef,#b9c2cc)" role="img" aria-label="Client portrait"></div>
  <span class="abs client-name" style="left:442px">CLIENT NAME HERE</span>

  <span class="abs dot" style="top:699px;background:var(--green)"></span>
  <span class="abs dot" style="top:710px"></span>
  <span class="abs dot" style="top:721px"></span>
</section>

<section>
  <h2 class="abs h2" style="left:55px;top:911px;font-size:17px">Meet Our <em>Doctors</em></h2>
  <a class="abs nav-circle" style="left:264px;top:911px;background:var(--blue-deep)" href="#"><svg width="6" height="6" viewBox="0 0 6 6"><path d="M4 1 L2 3 L4 5" fill="none" stroke="#fff" stroke-width="1"/></svg></a>
  <div class="abs doc-ring"></div>
  <div class="abs doc-inner"></div>
  <div class="abs doc-photo" role="img" aria-label="Portrait of Dr. Dana Whitfield"></div>
  <span class="abs zoom"><svg width="12" height="12" viewBox="0 0 12 12"><circle cx="5" cy="5" r="3.3" fill="none" stroke="#48d6a4" stroke-width="1.3"/><line x1="7.5" y1="7.5" x2="10.5" y2="10.5" stroke="#48d6a4" stroke-width="1.5"/></svg></span>
  <a class="abs nav-circle" style="left:449px;top:911px;background:var(--green)" href="#"><svg width="6" height="6" viewBox="0 0 6 6"><path d="M2 1 L4 3 L2 5" fill="none" stroke="#fff" stroke-width="1"/></svg></a>
  <h2 class="abs h2" style="right:55px;top:911px;font-size:17px">Dana Whitfield, <em>M.D.</em></h2>
</section>

<footer>
  <div class="abs footer"></div>
  <div class="abs foot-col" style="left:54px"><h4>FOR PATIENTS</h4><ul>
    <li>About Your Visit</li><li>Why Choose Us?</li><li>Patient Forms</li><li>Billing and Insurance</li><li>Locations and Maps</li><li>Appointments</li></ul></div>
  <div class="abs foot-col" style="left:229px"><h4>FOR PATIENTS</h4><ul>
    <li>Home</li><li>About Us</li><li>Our Physicians</li><li>For Physicians</li><li>Disclaimer</li><li>HIPAA</li><li>Log-In</li></ul></div>
  <div class="abs foot-col" style="left:393px"><h4>FOR PATIENTS</h4><ul>
    <li>Our Services</li><li>Mammography</li><li>MRI</li><li>CT-64</li><li>X-Ray</li><li>Nuclear Medicine</li><li>PET</li><li>Ultrasound</li></ul></div>
  <div class="abs foot-col contact" style="left:555px"><h4>CONTACT US</h4><ul>
    <li><svg viewBox="0 0 10 10"><path d="M2 1 L4 1 L4.5 3.5 L3.3 4.3 Q4.3 6.3 5.7 6.7 L6.5 5.5 L9 6 L9 8 Q9 9 8 9 Q1 8 1 2 Q1 1 2 1Z" fill="#fff"/></svg>(555) 014-2201 - Main Line</li>
    <li><svg viewBox="0 0 10 10"><rect x="1" y="2" width="8" height="7" fill="none" stroke="#fff"/><line x1="1" y1="4" x2="9" y2="4" stroke="#fff"/></svg>(555) 014-2202 - Scheduling</li>
    <li><svg viewBox="0 0 10 10"><rect x="0.5" y="2" width="9" height="6" rx="1" fill="#fff"/><rect x="0.5" y="4" width="9" height="1.2" fill="#4a84e0"/></svg>(555) 014-2203 - Billing</li>
    <li><svg viewBox="0 0 10 10"><rect x="2" y="1" width="6" height="8" fill="none" stroke="#fff"/><line x1="3.5" y1="4" x2="6.5" y2="4" stroke="#fff"/><line x1="3.5" y1="6" x2="6.5" y2="6" stroke="#fff"/></svg>(555) 014-2204 - Medical Records</li></ul></div>
  <div class="abs copyright">&copy; 2016 Pine Hollow Imaging Partners</div>
</footer>

</body>
</html>
```